Business Card Design Project

The business card is for an educational company that provides personalised tuition to students.

The company logo is in orange and blue (as provided) and should be included in the name card design

The philosophy of the company is to make learning a comfortable experience for student as such design of the namecard should look fresh and has a bit of the 'wow' factor. Some of the namecard design that appeals to me are as uploaded under Sample Design.

The particulars that need to be provided are:
(1): Company Name (Lantern Education)
(1): Name
(2): Educational qualifications which will appear below name
(3): Mobile number
(4): Email address
(5): Website

Industry/Entity Type

Business

Requirements
Must have
• (1): Company Logo

(2): The card background should preferably be coloured both for the front side and back.

(3): The choice of font is important as part of the selection consideration. There is no preferred font that I have selected, designer is free to choose the font that will complement their design.

```html
<!DOCTYPE html>
<html lang="en">
<head>
<meta charset="utf-8">
<title>Lantern Education – Business Cards</title>
<link href="https://fonts.googleapis.com/css2?family=Sorts+Mill+Goudy&display=swap" rel="stylesheet">
<style>
  :root {
    --backdrop: #2b2b2d;
    --orange: #f28f25;
    --orange-light: #f6a23a;
    --orange-deep: #e0601c;
    --rust: #d8521e;
    --blue: #3a9fdb;
    --white: #ffffff;
    --rule: rgba(255, 255, 255, 0.75);
  }
  * { box-sizing: border-box; margin: 0; padding: 0; }
  html, body {
    width: 1200px;
    height: 900px;
    overflow: hidden;
    background: var(--backdrop);
    font-family: "Sorts Mill Goudy", Georgia, serif;
    color: var(--white);
  }
  .canvas {
    position: relative;
    width: 1200px;
    height: 900px;
  }
  .card {
    position: absolute;
    left: 320px;
    width: 560px;
    height: 320px;
    overflow: hidden;
  }

  /* Front card */
  .card--front {
    top: 105px;
    background: radial-gradient(ellipse at 45% 40%, var(--orange-light) 0%, var(--orange) 45%, var(--orange-deep) 100%);
  }
  .brand {
    position: absolute;
    display: flex;
    align-items: center;
  }
  .brand__mark {
    flex: none;
    background: var(--white);
    border-radius: 6px;
  }
  .brand__name {
    line-height: 0.95;
    color: var(--white);
    font-weight: 400;
  }
  .card--front .brand {
    left: 140px;
    top: 105px;
    gap: 22px;
  }
  .card--front .brand__mark { width: 64px; height: 64px; }
  .card--front .brand__name { font-size: 44px; }
  .card--front .website {
    position: absolute;
    left: 0;
    right: 0;
    bottom: 28px;
    text-align: center;
    font-size: 15px;
    letter-spacing: 0.5px;
  }

  /* Contact card */
  .card--contact {
    top: 475px;
    background: var(--blue);
  }
  .contact-panel {
    position: absolute;
    left: 0;
    top: 30px;
    right: 48px;
    bottom: 30px;
    background: var(--orange);
    border-radius: 0 34px 34px 0;
    box-shadow: inset 2px 3px 6px rgba(120, 50, 0, 0.45);
  }
  .card--contact .brand {
    left: 42px;
    top: 93px;
    gap: 14px;
  }
  .card--contact .brand__mark { width: 40px; height: 40px; }
  .card--contact .brand__name { font-size: 28px; }
  .divider {
    position: absolute;
    left: 258px;
    top: 48px;
    bottom: 48px;
    width: 1px;
    background: var(--rule);
  }
  .details {
    position: absolute;
    left: 282px;
    top: 26px;
  }
  .details__name {
    font-size: 27px;
    letter-spacing: 1px;
    line-height: 1;
  }
  .details__role {
    font-size: 15px;
    color: var(--rust);
    margin-left: 12px;
    margin-top: 2px;
  }
  .details__phones {
    margin-top: 24px;
    font-size: 15px;
    line-height: 1.4;
  }
  .details__label { color: var(--rust); }
  .details__web {
    margin-top: 18px;
    font-size: 15px;
    line-height: 1.45;
  }
</style>
</head>
<body>
<main class="canvas">
  <section class="card card--front" aria-label="Business card front">
    <div class="brand">
      <span class="brand__mark"></span>
      <span class="brand__name">Lantern<br>Education</span>
    </div>
    <p class="website">www.lanterneducation.com</p>
  </section>

  <section class="card card--contact" aria-label="Business card contact side">
    <div class="contact-panel">
      <div class="brand">
        <span class="brand__mark"></span>
        <span class="brand__name">Lantern<br>Education</span>
      </div>
      <span class="divider"></span>
      <div class="details">
        <h1 class="details__name">ALEX MARLOW</h1>
        <p class="details__role">General manager</p>
        <p class="details__phones">
          <span class="details__label">Phone:</span> 555 210 4832<br>
          <span class="details__label">Mobile:</span> 55501987
        </p>
        <p class="details__web">
          info@lanterneducation.com<br>
          www.lanterneducation.com
        </p>
      </div>
    </div>
  </section>
</main>
</body>
</html>
```